LB - WESITE NEEDED PAGE: Clean / Modern / Pro & Dynamic

Lantern-Brokers is a new insurance brokerage firm dealing exclusively with companies (BToB) providing the following property: Liabilities Insurance Insurances Automobile Insurance Insurances Construction% 26amp; Engineering Casualty Workmen 's Compensation Health Insurance Marime% 26amp; Transit Credit Insurance Young, Fast, Proactive and Dynamic we call ourselves Lantern-Brokers because we are a "start-up" willing to make a difference in the market, bringing modernity and speed to our industry, still too bureaucratic / procedural / opaque uninitiated. We need something respecting the colors of our orange logtype; blue; white; black; easy to scroll, with simple information on the company; - who we are - our team (with the pictures) - what we do - what we do - contact us, contact us (google map) Luanda (Angola) Small company, just need something flashy / professional / structured / modern.

Target Market(s)

BtoB; Oil and gas companies; French speaking copying established in Angola, all industrials, factories and importers of goods.

Industry/Entity Type

Insurance Broker

Font styles to use
Sans Serif

Colors

Designer to choose colors to be used in the design.

Requirements
Must have
• We need something respecting the colors of our orange logtype; blue; white; black; easy to scroll, with simple information on the company; - who we are - our team (with the pictures) - what we do - what we do - contact us, contact us (google map) Luanda (Angola) Small company, just need something flashy / professional / structured / modern.
Nice to have
• A page format
Should not have
• WE DO NOT WANT A REFER TO OUR LOGO, but a Home Page for our Website with the basics categories ... >> PLEASE CAREFULLY USE THE RIGHT COLOR OF THE LOGOTYPE which are the ones enclosed Orange / Turquoise / Black as per the business card .

```html
<!DOCTYPE html>
<html lang="en">
<head>
<meta charset="utf-8">
<title>Lantern-Brokers — Insurance Brokerage</title>
<link href="https://fonts.googleapis.com/css2?family=Exo+2:wght@600;700;800&family=Lato:ital,wght@0,400;0,700;0,900;1,400&display=swap" rel="stylesheet">
<style>
:root{
  --orange:#f26b2a;
  --orange-light:#ff8a4c;
  --red:#f5301f;
  --blue:#0a86d8;
  --blue-light:#13a6f0;
  --navy:#0f2740;
  --ink:#111;
  --text:#555;
  --pale:#f1f5f9;
  --white:#fff;
  --grey:#c9ccd0;
}
*{margin:0;padding:0;box-sizing:border-box}
html,body{width:1200px;height:3769px;overflow:hidden}
body{position:relative;background:var(--white);font-family:"Lato",sans-serif;color:var(--text)}
.display{font-family:"Exo 2",sans-serif;font-weight:800;text-transform:uppercase}
.btn{position:absolute;display:flex;align-items:center;justify-content:center;border-radius:20px;color:#fff;font-family:"Lato",sans-serif;font-weight:900;font-size:13px;letter-spacing:.6px;text-transform:uppercase;text-decoration:none}
.btn--orange{background:linear-gradient(90deg,var(--red),var(--orange-light))}
.btn--blue{background:linear-gradient(90deg,var(--blue),var(--blue-light))}

/* header */
.site-header{position:absolute;left:0;top:0;width:1200px;height:121px;background:#fff}
.brand{position:absolute;left:140px;top:22px;display:flex;align-items:center;gap:10px}
.brand__mark{width:42px;height:42px;border-radius:50%;background:var(--orange)}
.brand__name{font-family:"Exo 2",sans-serif;font-weight:700;font-size:19px;color:var(--orange);text-transform:uppercase}
.socials{position:absolute;display:flex;gap:10px}
.socials span{width:30px;height:30px;border-radius:50%;border:2px solid var(--orange);display:block}
.header-phone{position:absolute;left:958px;top:20px;display:flex;gap:10px;align-items:center}
.header-phone b{display:block;font-size:11px;color:var(--ink);font-weight:900}
.header-phone small{display:block;font-size:12px;color:var(--ink);font-weight:700}
.nav{position:absolute;top:84px;left:0;width:1200px;font-size:12px;font-weight:900;color:var(--ink);text-transform:uppercase}
.nav a{position:absolute;color:inherit;text-decoration:none}
.nav a.is-active{color:var(--orange)}

/* hero */
.hero{position:absolute;left:0;top:121px;width:1200px;height:523px;background:linear-gradient(90deg,#eef3f7 0%,#dfe6ec 40%,#7b8693 70%,#3a4048 100%)}
.hero__title{position:absolute;left:142px;top:133px;font-size:38px;line-height:42px;color:var(--ink);letter-spacing:.5px}
.hero__lead{position:absolute;left:142px;top:230px;font-size:28px;line-height:34px;font-style:italic;color:var(--ink);width:520px}

/* who we are */
.band{position:absolute;left:0;top:873px;width:1200px;height:1336px;background:var(--pale)}
.about{position:absolute;left:168px;top:718px;width:863px;height:389px;display:flex}
.about__photo{width:378px;height:389px;background:linear-gradient(135deg,#8aa3b6,#cfd8de 55%,#6f8a5c)}
.about__body{flex:1;background:linear-gradient(135deg,var(--orange-light),var(--red));padding:60px 34px 0 34px;color:#fff}
.about__body h2{font-size:30px;margin-bottom:14px}
.about__body .strong{font-weight:700;font-size:13.5px;line-height:20px;margin-bottom:12px}
.about__body p{font-size:13px;line-height:20.5px}

/* services */
.section-title{position:absolute;left:0;width:1200px;text-align:center;font-size:33px;color:var(--navy)}
.service{position:absolute;width:283px;height:317px;background:#fff;box-shadow:0 4px 18px rgba(15,39,64,.06);text-align:center}
.service__ring{position:absolute;left:78px;top:34px}
.service__icon{position:absolute;left:110px;top:66px}
.service h3{position:absolute;top:189px;left:0;width:100%;font-family:"Exo 2",sans-serif;font-weight:700;font-size:12.5px;color:var(--ink)}
.service p{position:absolute;top:218px;left:24px;right:24px;font-size:12.5px;line-height:22px}

/* team */
.member{position:absolute;width:300px;text-align:center}
.member__photo{width:248px;height:248px;border-radius:50%;margin:0 auto;background:linear-gradient(160deg,#eef0f2,#c4c9cf 55%,#2b3441);border:4px solid var(--grey)}
.member__photo.is-accent{border-color:var(--orange)}
.member h3{margin-top:34px;font-family:"Exo 2",sans-serif;font-weight:700;font-size:18px;color:var(--navy);text-transform:uppercase}
.member p{margin-top:12px;font-size:12.5px;line-height:20.5px;padding:0 32px}
.member__social{display:flex;justify-content:center;gap:8px;margin-top:14px}
.member__social span{width:27px;height:27px;border-radius:50%;background:var(--grey)}

/* contact */
.map{position:absolute;left:0;top:3318px;width:1200px;height:395px;background:
  radial-gradient(ellipse 260px 140px at 180px 120px,rgba(255,255,255,.55),transparent 70%),
  radial-gradient(ellipse 300px 160px at 1000px 260px,rgba(255,255,255,.5),transparent 70%),
  radial-gradient(ellipse 220px 120px at 620px 300px,rgba(180,184,190,.45),transparent 70%),
  linear-gradient(135deg,#e4e6e9,#d2d5d9 50%,#e6e8ea)}
.map__badge{position:absolute;left:575px;top:3514px;width:52px;height:52px;background:#fff;border-radius:6px;box-shadow:0 3px 10px rgba(0,0,0,.18);display:flex;align-items:center;justify-content:center}
.map__badge span{width:30px;height:30px;border-radius:50%;background:var(--orange)}
.map__pin{position:absolute;left:593px;top:3592px}
.inquiry{position:absolute;left:211px;top:3072px;width:379px;height:388px;background:#fff;padding:52px 33px 0}
.inquiry h2{font-size:31px;color:var(--navy);margin-bottom:18px}
.field{height:34px;border:1px solid #dde2e7;margin-bottom:13px;display:flex;align-items:center;padding-left:14px;gap:10px;font-size:12.5px;color:#555}
.contact{position:absolute;left:590px;top:3072px;width:376px;height:388px;background:linear-gradient(135deg,var(--orange-light),var(--red));color:#fff;padding:52px 33px 0}
.contact h2{font-size:29px;margin-bottom:22px}
.contact__row{display:flex;gap:24px;margin-bottom:24px}
.contact__row svg{flex:0 0 38px}
.contact__row b{display:block;font-family:"Exo 2",sans-serif;font-weight:700;font-size:15px;text-transform:uppercase;margin-bottom:6px}
.contact__row span{font-size:12px;line-height:19px}

.footer{position:absolute;left:0;top:3713px;width:1200px;height:56px;background:#fff}
.footer p{position:absolute;left:143px;top:21px;font-size:11px;color:var(--ink)}
</style>
</head>
<body>

<header class="site-header">
  <div class="brand"><span class="brand__mark"></span><span class="brand__name">Lantern-Brokers</span></div>
  <div class="socials" style="left:826px;top:22px"><span></span><span></span><span></span></div>
  <div class="header-phone">
    <svg width="18" height="30" viewBox="0 0 18 30"><rect x="1.5" y="1.5" width="15" height="27" rx="3" fill="none" stroke="#f26b2a" stroke-width="2"/><line x1="6" y1="24" x2="12" y2="24" stroke="#f26b2a" stroke-width="2"/></svg>
    <div><b>PHONE</b><small>123 456 7710</small></div>
  </div>
  <nav class="nav">
    <a class="is-active" style="left:543px">Home</a>
    <a style="left:620px">Who We Are</a>
    <a style="left:746px">What We Do</a>
    <a style="left:870px">Our Team</a>
    <a style="left:977px">Contact Us</a>
  </nav>
</header>

<section class="hero" role="img" aria-label="Two businessmen reviewing work together in a bright office">
  <h1 class="hero__title display">Young, Fast, Proactive<br>&amp; Dynamic</h1>
  <p class="hero__lead">We are Insurance brokerage firm dealing exclusively with companies</p>
  <a class="btn btn--orange" style="left:142px;top:322px;width:176px;height:35px">Contact Us Today</a>
</section>

<div class="band"></div>

<section class="about">
  <div class="about__photo" role="img" aria-label="Team meeting in an office with a presentation on a screen"></div>
  <div class="about__body">
    <h2 class="display">Who We Are</h2>
    <p class="strong">Lorem ipsum dolor amet, enim ad minim veniam, quis nostrud exerci tation ullamcorper suscipit lobortis</p>
    <p>Lorem ipsum dolor sit amet, consectetuer adipiscing elit, sed diam nonummy nibh euismod tincidunt ut laoreet dolore magna aliquam erat volutpat. Ut wisi enim ad minim veniam, quis nostrud exerci tation ullamcorper suscipit lobortis nisl ut aliquip ex ea commodo consequat duis autem vel eum iriure dolor</p>
    <a class="btn btn--blue" style="position:relative;display:inline-flex;margin-top:20px;width:176px;height:36px">Contact Us Today</a>
  </div>
</section>

<h2 class="section-title display" style="top:1207px">What We Do</h2>

<article class="service" style="left:140px;top:1305px">
  <svg class="service__ring" width="128" height="128" viewBox="0 0 128 128"><path d="M86 8 A58 58 0 1 1 30 20" fill="none" stroke="#f26b2a" stroke-width="5" stroke-linecap="round"/></svg>
  <svg class="service__icon" width="64" height="64" viewBox="0 0 64 64" fill="none" stroke="#0a86d8" stroke-width="2" stroke-linejoin="round" stroke-linecap="round">
    <path d="M14 26 A18 18 0 0 1 50 26 Q45.5 22 41 26 Q36.5 22 32 26 Q27.5 22 23 26 Q18.5 22 14 26Z"/>
    <path d="M32 8 V6 M32 26 V38 Q32 41 29 41"/>
    <path d="M8 44 H16 V58 H8Z M16 46 H26 L34 49 H28 M16 55 H34 L50 47 Q53 45 51 43 L40 48"/>
  </svg>
  <h3>Liabilities Insurance</h3>
  <p>Lorem ipsum dolor sit amet, enim ad minim veniam, quis nostrud exerci tation ullamcorper suscipit lobortis.</p>
</article>
<article class="service" style="left:458px;top:1305px">
  <svg class="service__ring" width="128" height="128" viewBox="0 0 128 128"><path d="M86 8 A58 58 0 1 1 30 20" fill="none" stroke="#f26b2a" stroke-width="5" stroke-linecap="round"/></svg>
  <svg class="service__icon" width="64" height="64" viewBox="0 0 64 64" fill="none" stroke="#0a86d8" stroke-width="2" stroke-linejoin="round" stroke-linecap="round">
    <path d="M38 6 L50 10 V20 Q50 29 38 34 Q26 29 26 20 V10Z"/>
    <path d="M33 19 L37 23 L44 15"/>
    <path d="M6 50 V42 Q6 39 10 38 L16 30 H30 L36 38 H42 Q46 39 46 42 V50 Z"/>
    <circle cx="14" cy="51" r="4"/><circle cx="38" cy="51" r="4"/>
  </svg>
  <h3>Automobile Insurance</h3>
  <p>Lorem ipsum dolor sit amet, enim ad minim veniam, quis nostrud exerci tation ullamcorper suscipit lobortis.</p>
</article>
<article class="service" style="left:775px;top:1305px">
  <svg class="service__ring" width="128" height="128" viewBox="0 0 128 128"><path d="M86 8 A58 58 0 1 1 30 20" fill="none" stroke="#f26b2a" stroke-width="5" stroke-linecap="round"/></svg>
  <svg class="service__icon" width="64" height="64" viewBox="0 0 64 64" fill="none" stroke="#0a86d8" stroke-width="2" stroke-linejoin="round" stroke-linecap="round">
    <path d="M8 22 Q8 10 20 10 Q32 10 32 22 Z M5 22 H35"/>
    <path d="M10 58 V36 H30 V58 M16 36 V58 M24 36 V58"/>
    <path d="M42 58 V10 H48 V58 M42 18 L58 14 M48 14 L58 14 M56 14 V26 M40 58 H60"/>
  </svg>
  <h3>Construction &amp; Engineering Insurance</h3>
  <p>Lorem ipsum dolor sit amet, enim ad minim veniam, quis nostrud exerci tation ullamcorper suscipit lobortis.</p>
</article>
<article class="service" style="left:140px;top:1687px">
  <svg class="service__ring" width="128" height="128" viewBox="0 0 128 128"><path d="M86 8 A58 58 0 1 1 30 20" fill="none" stroke="#f26b2a" stroke-width="5" stroke-linecap="round"/></svg>
  <svg class="service__icon" width="64" height="64" viewBox="0 0 64 64" fill="none" stroke="#0a86d8" stroke-width="2" stroke-linejoin="round" stroke-linecap="round">
    <path d="M44 6 L56 10 V20 Q56 29 44 34 Q32 29 32 20 V10Z"/>
    <path d="M39 19 L43 23 L50 15"/>
    <path d="M6 56 L16 38 L26 56 Z M16 45 V50 M16 53 V53.5"/>
    <path d="M30 58 H58 M50 58 V42"/>
  </svg>
  <h3>Casualty Workmen 's Compensation</h3>
  <p>Lorem ipsum dolor sit amet, enim ad minim veniam, quis nostrud exerci tation ullamcorper suscipit lobortis.</p>
</article>
<article class="service" style="left:458px;top:1687px">
  <svg class="service__ring" width="128" height="128" viewBox="0 0 128 128"><path d="M86 8 A58 58 0 1 1 30 20" fill="none" stroke="#f26b2a" stroke-width="5" stroke-linecap="round"/></svg>
  <svg class="service__icon" width="64" height="64" viewBox="0 0 64 64" fill="none" stroke="#0a86d8" stroke-width="2" stroke-linejoin="round" stroke-linecap="round">
    <rect x="18" y="12" width="36" height="28" rx="3"/>
    <path d="M30 12 V7 H42 V12"/>
    <path d="M36 18 V34 M28 26 H44"/>
    <path d="M6 46 H14 V58 H6Z M14 48 H24 L32 51 H26 M14 56 H32 L50 48 Q53 46 51 44 L40 49"/>
  </svg>
  <h3>Health Insurance</h3>
  <p>Lorem ipsum dolor sit amet, enim ad minim veniam, quis nostrud exerci tation ullamcorper suscipit lobortis.</p>
</article>
<article class="service" style="left:775px;top:1687px">
  <svg class="service__ring" width="128" height="128" viewBox="0 0 128 128"><path d="M86 8 A58 58 0 1 1 30 20" fill="none" stroke="#f26b2a" stroke-width="5" stroke-linecap="round"/></svg>
  <svg class="service__icon" width="64" height="64" viewBox="0 0 64 64" fill="none" stroke="#0a86d8" stroke-width="2" stroke-linejoin="round" stroke-linecap="round">
    <rect x="24" y="8" width="8" height="8"/><rect x="32" y="8" width="8" height="8"/>
    <rect x="20" y="16" width="10" height="8"/><rect x="30" y="16" width="10" height="8"/><rect x="40" y="16" width="8" height="8"/>
    <path d="M12 24 H54 L48 36 H18 Z"/>
    <path d="M6 46 H14 V58 H6Z M14 48 H24 L32 51 H26 M14 56 H32 L50 48 Q53 46 51 44 L40 49"/>
  </svg>
  <h3>Marime &amp; Transit Credit Insurance</h3>
  <p>Lorem ipsum dolor sit amet, enim ad minim veniam, quis nostrud exerci tation ullamcorper suscipit lobortis.</p>
</article>

<a class="btn btn--blue" style="left:512px;top:2066px;width:190px;height:36px">Contact Us Today</a>

<h2 class="section-title display" style="top:2305px">Our Team</h2>

<div class="member" style="left:168px;top:2451px">
  <div class="member__photo is-accent" role="img" aria-label="Portrait of a senior team member in a suit"></div>
  <h3>Dr. Marcel Oduya</h3>
  <p>Advanced Medical and Surgical Glaucoma Managment, Minimally Invasive Glaucoma Surgery</p>
  <div class="member__social"><span style="background:var(--blue)"></span><span style="background:var(--blue-light)"></span><span style="background:var(--blue)"></span></div>
</div>
<div class="member" style="left:450px;top:2451px">
  <div class="member__photo" role="img" aria-label="Portrait of a team member wearing glasses"></div>
  <h3>Dr. Clara Menezes</h3>
  <p>Advanced Medical and Surgical Glaucoma Management, Minimally Invasive Glaucoma Surgery,...</p>
  <div class="member__social"><span></span><span></span><span></span></div>
</div>
<div class="member" style="left:731px;top:2451px">
  <div class="member__photo" role="img" aria-label="Portrait of a smiling team member"></div>
  <h3>Dr. Tiago Ferraz</h3>
  <p>All-Laser Cataract Surgery, Refractive Surgery, Comprehensive Ophthalmology</p>
  <div class="member__social"><span></span><span></span><span></span></div>
</div>

<a class="btn btn--blue" style="left:505px;top:2927px;width:190px;height:37px">Contact Us Today</a>

<div class="map" role="img" aria-label="Street map of the city showing the office location"></div>
<div class="map__badge"><span></span></div>
<svg class="map__pin" width="18" height="24" viewBox="0 0 18 24"><path d="M9 23 C3 15 1 12 1 8 A8 8 0 0 1 17 8 C17 12 15 15 9 23Z" fill="#f5301f"/><circle cx="9" cy="8" r="3" fill="#fff"/></svg>

<section class="inquiry">
  <h2 class="display">Quick Inquiry</h2>
  <div class="field"><svg width="10" height="11" viewBox="0 0 10 11"><circle cx="5" cy="3" r="2.6" fill="#f5301f"/><path d="M0 11 Q0 6 5 6 Q10 6 10 11Z" fill="#f5301f"/></svg>Name</div>
  <div class="field"><svg width="10" height="10" viewBox="0 0 10 10"><path d="M1 1 L3.5 0.5 L4.5 3 L3 4 Q4 6 6 7 L7 5.5 L9.5 6.5 L9 9 Q3 9.5 1 1Z" fill="#f5301f"/></svg>Phone</div>
  <div class="field"><svg width="11" height="9" viewBox="0 0 11 9"><rect x="0" y="0" width="11" height="9" rx="1" fill="#f5301f"/><path d="M0.5 1 L5.5 5 L10.5 1" fill="none" stroke="#fff" stroke-width="1"/></svg>Email</div>
  <div class="field"><svg width="11" height="10" viewBox="0 0 11 10"><rect x="0.5" y="1.5" width="8" height="8" fill="none" stroke="#f5301f"/><path d="M4 6 L10 0.5" stroke="#f5301f" stroke-width="1.5"/></svg>Message</div>
  <a class="btn btn--blue" style="position:relative;display:flex;margin-top:8px;width:142px;height:38px">Submit</a>
</section>

<section class="contact">
  <h2 class="display">Contact Us</h2>
  <div class="contact__row">
    <svg width="38" height="44" viewBox="0 0 38 44"><path d="M19 42 C8 28 5 22 5 16 A14 14 0 0 1 33 16 C33 22 30 28 19 42Z" fill="none" stroke="#fff" stroke-width="2"/><circle cx="19" cy="16" r="5" fill="none" stroke="#fff" stroke-width="2"/></svg>
    <div><b>Address</b><span>123 Building Name, Street Name<br>City, State XY 123-456</span></div>
  </div>
  <div class="contact__row">
    <svg width="38" height="44" viewBox="0 0 38 44"><rect x="10" y="2" width="18" height="40" rx="3" fill="none" stroke="#fff" stroke-width="2"/><line x1="16" y1="36" x2="22" y2="36" stroke="#fff" stroke-width="2"/></svg>
    <div><b>Phone</b><span>123 456 7710</span></div>
  </div>
  <div class="contact__row">
    <svg width="38" height="30" viewBox="0 0 38 30"><rect x="2" y="3" width="34" height="24" fill="none" stroke="#fff" stroke-width="2"/><path d="M2 3 L19 17 L36 3" fill="none" stroke="#fff" stroke-width="2"/></svg>
    <div><b>Email</b><span>inquiry@lanternbrokers.com</span></div>
  </div>
</section>

<footer class="footer">
  <p>Copyright © 2019 Lantern Brokers. All Rights Reserved.</p>
  <div class="socials" style="left:948px;top:13px"><span></span><span></span><span></span></div>
</footer>

</body>
</html>
```